Tidewell Homecare

I am looking to have a website designed for a housekeeping company that looks similar to this one. https://marloweshomecare.example/

I need 5 websites designed but will start with this one to see how I like it.

Industry/Entity Type

House Cleaning

Coding

Coded - Design and coding required

Number of Pages Required

5+ page

Font styles to use
Serif
Script

Colors
ffffff
fdf9cf
fbf289
fbee3f
d6edf3
86cae7
33a6d7
edf1f8
cedeed

```html
<!DOCTYPE html>
<html lang="en">
<head>
<meta charset="utf-8">
<title>Tidewell Homecare</title>
<link href="https://fonts.googleapis.com/css2?family=Libre+Franklin:wght@300;400;500;600;700;800&display=swap" rel="stylesheet">
<style>
:root{
  --white:#ffffff;
  --cream:#fdf9cf;
  --cream-soft:#fbf6c4;
  --yellow:#fbee3f;
  --blue:#2f8fd3;
  --blue-bright:#33a6d7;
  --blue-deep:#2268b8;
  --ink:#1b1b1b;
  --text:#3a3a3a;
  --dark:#1f1f21;
  --light-bg:#edf1f8;
}
*{box-sizing:border-box;margin:0;padding:0}
html,body{width:1200px;height:4819px;overflow:hidden}
body{font-family:"Libre Franklin",Arial,sans-serif;color:var(--text);background:var(--white);position:relative}
.abs{position:absolute}
.page{position:relative;width:1200px;height:4819px;overflow:hidden}

/* hero */
.hero{left:0;top:0;width:1200px;height:780px;background:linear-gradient(120deg,#5a5148 0%,#7d7267 35%,#9c928a 60%,#6e655d 100%)}
.hero-shade{left:0;top:0;width:1200px;height:780px;background:rgba(20,18,16,.35)}
.brand{left:144px;top:28px;display:flex;align-items:center;gap:14px;color:var(--white)}
.brand-mark{width:70px;height:70px;border:3px solid var(--white);border-radius:50%}
.brand-name{font-weight:800;font-size:27px;line-height:1;letter-spacing:.5px;text-transform:uppercase}
.brand-name small{display:block;font-size:18px;font-weight:800;margin-top:4px}
.topbar{left:672px;top:20px;display:flex;align-items:center;gap:22px}
.phone{display:flex;align-items:center;gap:10px;color:var(--white);font-weight:600;font-size:16px}
.phone-ico{width:30px;height:30px;border-radius:50%;background:var(--white);display:flex;align-items:center;justify-content:center}
.btn-est{background:var(--blue-bright);color:var(--white);font-size:14px;font-weight:700;padding:12px 18px;text-transform:uppercase}
.nav{left:513px;top:96px;display:flex;gap:30px;font-size:13px;font-weight:700;color:var(--white);text-transform:uppercase}
.nav .on{color:var(--yellow)}
.hero-title{left:0;top:296px;width:1200px;text-align:center;color:var(--white);font-weight:800;font-size:48px;text-transform:uppercase}
.hero-text{left:300px;top:360px;width:600px;text-align:center;color:var(--white);font-size:17px;line-height:24px}
.btn-hero{left:524px;top:455px;width:152px;height:40px;background:var(--blue-bright);color:var(--white);font-size:14px;font-weight:700;display:flex;align-items:center;justify-content:center;text-transform:uppercase}
.dots{left:567px;top:721px;display:flex;gap:8px}
.dots span{width:16px;height:16px;border-radius:50%;border:2px solid var(--white)}
.dots span.on{background:var(--white)}

/* service panels */
.panels{left:0;top:700px;width:1200px;height:504px}
.panel{top:0;width:600px;height:504px;text-align:center}
.panel-title{font-weight:700;font-size:23px;line-height:27px;text-transform:uppercase}
.panel-text{font-size:15px;line-height:25.5px;margin:26px auto 0;width:370px}
.panel-btn{display:inline-block;margin-top:28px;font-size:13px;font-weight:700;padding:11px 22px;text-transform:uppercase}
.panel.res{left:0;color:var(--ink)}
.panel.res .panel-title{margin-top:208px}
.panel.res .panel-btn{background:var(--ink);color:var(--white)}
.panel.com{left:600px;color:var(--white)}
.panel.com .panel-title{margin-top:208px}
.panel.com .panel-text{color:#d5e8f5}
.panel.com .panel-btn{border:2px solid var(--white);color:var(--white)}
.panel-ico{left:240px;top:100px}

/* welcome */
.welcome-photo{left:146px;top:1305px;width:384px;height:408px;border-radius:50%;background:radial-gradient(circle at 45% 40%,#d9d2cb,#b9aea5 55%,#8b7d73);border-bottom:5px solid var(--yellow)}
.welcome-sub{left:588px;top:1314px;font-size:38px;font-weight:300;color:var(--ink)}
.welcome-title{left:588px;top:1360px;font-size:38px;font-weight:600;color:var(--ink)}
.rule{height:4px;width:74px;background:var(--blue-bright)}
.welcome-text{left:588px;top:1462px;width:470px;font-size:13.8px;line-height:24px;color:var(--text)}
.btn-outline{border:2px solid var(--blue-bright);color:var(--blue-bright);font-size:13px;font-weight:700;display:flex;align-items:center;justify-content:center;text-transform:uppercase}

/* services */
.services{left:0;top:1755px;width:1200px;height:845px;background:radial-gradient(ellipse at 50% 40%,#2c2c2f,#18181a 75%)}
.services-title{left:0;top:1912px;width:1200px;text-align:center;color:var(--white);font-size:38px;font-weight:800;text-transform:uppercase}
.card{top:2039px;width:298px;height:441px;background:var(--white)}
.card h3{font-size:17px;font-weight:700;line-height:23px;color:var(--ink);text-transform:uppercase}
.card p{font-size:13.5px;line-height:21.5px;color:var(--text)}
.card-photo{position:absolute;left:0;width:100%}
.card-ico{position:absolute}

/* hard work */
.hardwork{left:0;top:2598px;width:1200px;height:455px;background:linear-gradient(90deg,#b9a694 0%,#d7cfc6 35%,#ebe9e6 55%,#efeeec 100%)}
.hw-photo{left:0;top:2598px;width:600px;height:455px;background:linear-gradient(90deg,#9e8670,#c8bdb0 60%,rgba(235,233,230,0))}
.hw-title{left:655px;top:2694px;font-size:38px;font-weight:600;color:var(--ink)}
.hw-text{left:657px;top:2785px;width:420px;font-size:13.8px;line-height:24px}
.btn-solid{background:var(--blue-bright);color:var(--white);font-size:13px;font-weight:700;display:flex;align-items:center;justify-content:center;text-transform:uppercase}

/* estimate */
.est-title{left:144px;top:3132px;font-size:38px;font-weight:700;color:var(--ink)}
.est-box{left:140px;top:3226px;width:680px;height:411px;background:#f5f5f5;border-top:4px solid var(--blue-bright);border-left:4px solid var(--blue-bright)}
.field{position:absolute;height:38px;background:var(--white);border:1px solid #cfcfcf;font-size:11.5px;color:#444;padding:12px 14px}
.btn-submit{position:absolute;left:42px;top:320px;width:576px;height:40px;background:var(--blue);color:var(--white);font-weight:700;font-size:15px;display:flex;align-items:center;justify-content:center;text-transform:uppercase}
.est-photo{left:760px;top:3228px;width:300px;height:520px;background:linear-gradient(180deg,#6b4a36 0%,#c89e86 30%,#2e55b0 60%,#24479a 100%);border-radius:150px 150px 0 0}

/* testimonials */
.testi{left:0;top:3748px;width:1200px;height:600px;background:linear-gradient(180deg,#2b6ec5,#2a73cb 60%,#3b86d8)}
.testi-title{left:0;top:3818px;width:1200px;text-align:center;color:var(--white);font-size:37px;font-weight:700;text-transform:uppercase}
.testi-photo{left:227px;top:3946px;width:191px;height:191px;border-radius:50%;border:4px solid var(--white);background:radial-gradient(circle at 50% 40%,#d7c8b6,#8e9aa8)}
.quote{color:var(--white);font-size:90px;font-weight:800;line-height:1;font-family:Georgia,serif}
.testi-text{left:509px;top:3962px;width:470px;color:var(--white);font-size:13.5px;line-height:22.5px}
.testi-name{left:509px;top:4105px;color:var(--white);font-size:14.5px}
.stars{left:509px;top:4130px;color:var(--white);font-size:16px;letter-spacing:2px}

/* footer */
.footer{left:0;top:4287px;width:1200px;height:403px;background:var(--cream)}
.foot-h{font-size:17px;font-weight:700;color:var(--ink);text-transform:uppercase}
.foot-t{font-size:12.5px;line-height:20px;color:var(--text)}
.foot-input{position:absolute;width:272px;height:38px;border-radius:19px;background:var(--white);border:1px solid #ddd;font-size:12px;color:#555;padding:11px 14px}
.contact-row{position:absolute;display:flex;gap:14px;font-size:13.5px;line-height:20px;color:var(--ink)}
.links a{display:block;font-size:12.5px;color:var(--ink);text-decoration:none;line-height:25px}
.foot-brand{left:930px;top:4410px;text-align:center;color:var(--ink);font-weight:800;font-size:30px;line-height:1;text-transform:uppercase}
.foot-brand small{display:block;font-size:16px;margin-top:4px}
.foot-brand .mark{width:64px;height:64px;border:3px solid var(--blue-bright);border-radius:50%;margin:0 auto 12px}
.bottom{left:0;top:4690px;width:1200px;height:129px;background:var(--white)}
.copy{left:149px;top:4745px;font-size:13px;color:var(--ink)}
.socials{left:906px;top:4734px;display:flex;gap:6px}
.socials span{width:32px;height:32px;border-radius:50%;border:2px solid var(--blue-bright)}
.socials span.red{border-color:#c84a4a}
</style>
</head>
<body>
<div class="page">

  <!-- hero -->
  <div class="abs hero" role="img" aria-label="Photo of a smiling housekeeper wiping a kitchen counter"></div>
  <div class="abs hero-shade"></div>
  <div class="abs brand"><span class="brand-mark"></span><div class="brand-name">Tidewell<small>Homecare</small></div></div>
  <div class="abs topbar">
    <div class="phone"><span class="phone-ico"><svg width="16" height="16" viewBox="0 0 24 24"><path fill="#5a5148" d="M6.6 10.8a15 15 0 006.6 6.6l2.2-2.2c.3-.3.7-.4 1-.2 1.1.4 2.3.6 3.6.6.6 0 1 .4 1 1V20c0 .6-.4 1-1 1A17 17 0 013 4c0-.6.4-1 1-1h3.5c.6 0 1 .4 1 1 0 1.2.2 2.4.6 3.6.1.3 0 .7-.2 1z"/></svg></span>CALL 555 0142 7788</div>
    <div class="btn-est">Free Estimate</div>
  </div>
  <nav class="abs nav"><span class="on">Home</span><span>About Us</span><span>Services</span><span>Gift Cards</span><span>Blog</span><span>Contact Us</span></nav>
  <h1 class="abs hero-title">Tidewell Homecare</h1>
  <p class="abs hero-text">Lorem ipsum dolor sit amet, consectetur adipiscing elit, sed do eiusmod tempor incididunt ut labore et dolore magna aliqua. Ut enim ad minim veniam, quis nostrud exercitation ullamco</p>
  <div class="abs btn-hero">Learn More</div>
  <div class="abs dots"><span class="on"></span><span></span><span></span></div>

  <!-- panels -->
  <svg class="abs" style="left:0;top:700px" width="1200" height="504" viewBox="0 0 1200 504">
    <path d="M0 10 C200 30 420 60 600 85 L600 504 L0 504Z" fill="#fbf6c4"/>
    <path d="M600 85 C800 60 1000 30 1200 8 L1200 504 L600 504Z" fill="#2f8fd3"/>
  </svg>
  <div class="abs panels">
    <div class="abs panel res">
      <svg class="abs panel-ico" style="left:270px;top:108px" width="84" height="80" viewBox="0 0 84 80" fill="none" stroke="#1b1b1b" stroke-width="3">
        <rect x="10" y="40" width="64" height="26" rx="4"/><path d="M16 66v8M68 66v8M18 40V30h48v10"/><rect x="14" y="4" width="26" height="22"/><path d="M58 26V12h12l-4-8h-4zM52 28h24"/>
      </svg>
      <h2 class="panel-title">Residential<br>Cleaning</h2>
      <p class="panel-text">Sed ut perspiciatis unde omnis iste natus error sit voluptatem accusantium doloremque ladantium, totam rem aperiam, eaque ipsa quae ab illo inventore veritatis et quasi architecto</p>
      <span class="panel-btn">Residential Services</span>
    </div>
    <div class="abs panel com">
      <svg class="abs panel-ico" style="left:216px;top:90px" width="100" height="100" viewBox="0 0 100 100" fill="none" stroke="#fff" stroke-width="3">
        <path d="M16 58h50M20 58v36M20 70h16M20 82h16M36 58v36"/><rect x="46" y="28" width="20" height="16"/><path d="M72 46h14v12H72zM79 58v28M70 94h18M79 86v8"/><path d="M10 12l3 6 6 3-6 3-3 6-3-6-6-3 6-3z" fill="#fff"/>
      </svg>
      <h2 class="panel-title">Commercial<br>Office Cleaning</h2>
      <p class="panel-text">Sed ut perspiciatis unde omnis iste natus error sit voluptatem accusantium doloremque ladantium, totam rem aperiam, eaque ipsa quae ab illo inventore veritatis et quasi architecto</p>
      <span class="panel-btn">Commercial Services</span>
    </div>
  </div>

  <!-- welcome -->
  <div class="abs welcome-photo" role="img" aria-label="Photo of a housekeeper holding cleaning supplies and giving a thumbs up"></div>
  <div class="abs welcome-sub">Welcome to</div>
  <h2 class="abs welcome-title">Tidewell Homecare</h2>
  <div class="abs rule" style="left:590px;top:1432px"></div>
  <p class="abs welcome-text">Sed ut perspiciatis unde omnis iste natus error sit voluptatem accusantium doloremque laudantium, totam rem aperiam, eaque ipsa quae ab illo inventore veritatis et quasi architecto beatae vitae dicta sunt explicabo. Nemo enim ipsam voluptatem quia voluptas sit aspernatur aut odit aut fugit, sed quia consequuntur magni dolores eos qui ratione voluptatem sequi nesciunt. Neque porro quisquam est, qui dolorem ipsum quia dolor sit amet, consectetur, adipisci velit</p>
  <div class="abs btn-outline" style="left:589px;top:1655px;width:142px;height:40px">Learn More</div>

  <!-- services -->
  <div class="abs services"></div>
  <svg class="abs" style="left:0;top:1740px" width="1200" height="90" viewBox="0 0 1200 90">
    <path d="M0 0 H1200 V20 C900 80 300 80 0 20Z" fill="#fff"/>
    <path d="M0 20 C300 80 900 80 1200 20" stroke="#fbf6c4" stroke-width="5" fill="none"/>
  </svg>
  <h2 class="abs services-title">Our Services</h2>
  <div class="abs rule" style="left:563px;top:1978px;width:74px;background:#fff;height:3px"></div>

  <div class="abs card" style="left:125px">
    <h3 style="position:absolute;left:18px;top:30px">Residential<br>Cleaning</h3>
    <svg class="card-ico" style="left:205px;top:26px" width="66" height="66" viewBox="0 0 66 66"><circle cx="36" cy="30" r="26" fill="#fdf9cf"/><path d="M8 34L30 14l22 20M14 30v26h32V30M22 56V40h10v16M36 38h8v8h-8z" fill="none" stroke="#1b1b1b" stroke-width="2.5"/></svg>
    <p style="position:absolute;left:18px;top:122px;width:262px">Lorem ipsum dolor sit amet, consectetur adipiscing elit, sed do eiusmod tempor incididunt ut labore et dolore magna aliqua. Ut enim ad minim veniam, quis nostrud exercitation</p>
    <div class="card-photo" style="top:253px;height:188px;background:linear-gradient(160deg,#3a3028,#8a6f55 50%,#c9b8a4)" role="img" aria-label="Photo of a bright living room with a staircase"></div>
  </div>
  <div class="abs card" style="left:449px">
    <div class="card-photo" style="top:0;height:190px;background:linear-gradient(160deg,#e7e5e2,#a9a7a5 55%,#6a6866)" role="img" aria-label="Photo of a cleaner wiping an office desk"></div>
    <h3 style="position:absolute;left:20px;top:222px">Residential<br>Rental Cleaning</h3>
    <svg class="card-ico" style="left:202px;top:218px" width="80" height="64" viewBox="0 0 84 70" fill="none" stroke="#1b1b1b" stroke-width="3"><rect x="8" y="34" width="66" height="24" rx="4"/><path d="M14 58v8M68 58v8M16 34V24h50v10M56 22V8h10l-4-6h-4zM50 24h22"/></svg>
    <div class="rule" style="position:absolute;left:20px;top:290px;width:40px;height:3px"></div>
    <p style="position:absolute;left:20px;top:306px;width:262px">Lorem ipsum dolor sit amet, consectetur adipiscing elit, sed do eiusmod tempor incididunt ut labore et dolore magna aliqua. Ut enim ad minim veniam, quis nostrud exercitation</p>
  </div>
  <div class="abs card" style="left:773px">
    <h3 style="position:absolute;left:20px;top:32px">Additional<br>Cleaning</h3>
    <svg class="card-ico" style="left:200px;top:26px" width="68" height="68" viewBox="0 0 68 68"><rect x="18" y="10" width="40" height="48" fill="#fdf9cf"/><path d="M12 14h40v40H12zM20 46L46 20M40 22l8 8M18 54l8-14 6 6z" fill="none" stroke="#1b1b1b" stroke-width="2.5"/></svg>
    <p style="position:absolute;left:20px;top:124px;width:262px">Lorem ipsum dolor sit amet, consectetur adipiscing elit, sed do eiusmod tempor incididunt ut labore et dolore magna aliqua. Ut enim ad minim veniam, quis nostrud exercitation</p>
    <div class="card-photo" style="top:253px;height:188px;background:linear-gradient(160deg,#d8dde2,#9aa6b1 50%,#e3c84a)" role="img" aria-label="Photo of colorful cleaning sprays and gloves"></div>
  </div>

  <!-- hard work -->
  <div class="abs hardwork"></div>
  <div class="abs hw-photo" role="img" aria-label="Photo of a manager with a clipboard and a housekeeper cleaning in the background"></div>
  <h2 class="abs hw-title">Hard Work &amp; Reliability</h2>
  <p class="abs hw-text">Sed ut perspiciatis unde omnis iste natus error sit voluptatem accusantium doloremque laudantium, totam rem aperiam, eaque ipsa quae ab illo inventore veritatis et quasi architecto beatae vitae dicta sunt explicabo.</p>
  <div class="abs btn-solid" style="left:658px;top:2900px;width:142px;height:40px">Learn More</div>

  <!-- estimate -->
  <h2 class="abs est-title">Free Estimate</h2>
  <div class="abs rule" style="left:144px;top:3193px"></div>
  <div class="abs est-photo" role="img" aria-label="Photo of a smiling woman in a blue dress holding out her hand"></div>
  <div class="abs est-box">
    <div class="field" style="left:42px;top:44px;width:278px">First Name</div>
    <div class="field" style="left:340px;top:44px;width:278px">Last Name</div>
    <div class="field" style="left:42px;top:100px;width:278px">Phone Number</div>
    <div class="field" style="left:340px;top:100px;width:278px">Email Address</div>
    <div class="field" style="left:42px;top:156px;width:278px">Company Name</div>
    <div class="field" style="left:340px;top:156px;width:278px">Suburb</div>
    <div class="field" style="left:42px;top:212px;width:576px;height:84px">Message</div>
    <div class="btn-submit">Submit</div>
  </div>

  <!-- testimonials -->
  <div class="abs testi" role="img" aria-label="Blue-tinted photo of a cleaner at work"></div>
  <h2 class="abs testi-title">What Our Customers Say</h2>
  <div class="abs rule" style="left:565px;top:3888px;width:70px;background:#fff;height:3px"></div>
  <svg class="abs" style="left:150px;top:4016px" width="26" height="40" viewBox="0 0 26 40"><path d="M22 3L5 20l17 17" stroke="#fff" stroke-width="4" fill="none"/></svg>
  <svg class="abs" style="left:1024px;top:4016px" width="26" height="40" viewBox="0 0 26 40"><path d="M4 3l17 17L4 37" stroke="#fff" stroke-width="4" fill="none"/></svg>
  <div class="abs testi-photo" role="img" aria-label="Portrait photo of a customer"></div>
  <div class="abs quote" style="left:450px;top:3950px">“</div>
  <p class="abs testi-text">Lorem ipsum dolor sit amet, consectetur adipiscing elit, sed do eiusmod tempor incididunt ut labore et dolore magna aliqua. Ut enim ad minim veniam, quis nostrud exercitation ullamco laboris nisi ut aliquip ex ea commodo consequat. Duis aute irure dolor in reprehenderit in voluptate velit esse cillum dolore eu fugiat nulla pariatur. Excepteur sint occaecat cupidatat non proident, sunt in culpa qui officia</p>
  <div class="abs testi-name">Dana Reyes</div>
  <div class="abs stars">★★★★★</div>
  <div class="abs quote" style="left:614px;top:4104px">”</div>

  <!-- footer -->
  <div class="abs footer"></div>
  <svg class="abs" style="left:0;top:4268px" width="1200" height="70" viewBox="0 0 1200 70">
    <path d="M0 0 H1200 V60 C900 0 300 0 0 60Z" fill="#3b86d8"/>
    <path d="M40 62 C300 4 900 4 1160 62" stroke="#8a8a7a" stroke-width="3" fill="none"/>
  </svg>
  <h3 class="abs foot-h" style="left:145px;top:4364px">Sign Up For Newsletter</h3>
  <p class="abs foot-t" style="left:145px;top:4418px;width:290px">excepteur sint occaecat cupidatat non proident, sunt in culpa qui officia deserunt</p>
  <div class="foot-input" style="left:144px;top:4474px">Enter Name</div>
  <div class="foot-input" style="left:144px;top:4530px">Enter email</div>
  <div class="abs btn-solid" style="left:144px;top:4584px;width:140px;height:36px;border-radius:18px;background:var(--blue)">Subscribe</div>

  <h3 class="abs foot-h" style="left:462px;top:4364px">Contact Us</h3>
  <div class="contact-row" style="left:465px;top:4416px"><svg width="16" height="20" viewBox="0 0 16 20"><path d="M8 0a7 7 0 00-7 7c0 5 7 13 7 13s7-8 7-13a7 7 0 00-7-7zm0 10a3 3 0 110-6 3 3 0 010 6z" fill="#2f8fd3"/></svg><span>tidewellhomecare<br>48 Harbor Lane<br>Seacliff, California 90210</span></div>
  <div class="contact-row" style="left:465px;top:4498px"><svg width="16" height="16" viewBox="0 0 24 24"><path fill="#2f8fd3" d="M6.6 10.8a15 15 0 006.6 6.6l2.2-2.2c.3-.3.7-.4 1-.2 1.1.4 2.3.6 3.6.6.6 0 1 .4 1 1V20c0 .6-.4 1-1 1A17 17 0 013 4c0-.6.4-1 1-1h3.5c.6 0 1 .4 1 1 0 1.2.2 2.4.6 3.6.1.3 0 .7-.2 1z"/></svg><span>555-0199-2046</span></div>
  <div class="contact-row" style="left:465px;top:4536px"><svg width="18" height="14" viewBox="0 0 18 14"><rect width="18" height="14" rx="2" fill="#2f8fd3"/><path d="M1 2l8 6 8-6" stroke="#fdf9cf" stroke-width="1.6" fill="none"/></svg><span>info@tidewellhomecare.example</span></div>

  <h3 class="abs foot-h" style="left:762px;top:4364px">Quick Links</h3>
  <div class="abs links" style="left:766px;top:4418px"><a>Home</a><a>Services</a><a>Gift Cards</a><a>About</a><a>Contact Us</a></div>
  <div class="abs foot-brand"><div class="mark"></div>Tidewell<small>Homecare</small></div>

  <div class="abs bottom"></div>
  <div class="abs copy">Tidewell Homecare © 2020 All Rights Reserved | Privacy Policy</div>
  <div class="abs socials"><span></span><span></span><span></span><span class="red"></span></div>
</div>
</body>
</html>
```